ecommerce news podcast artwork

Podcast cover art for a podcast featuring daily news and events around ecommerce product businesses.

text to be: BRISK LOOP
optional third line of text with smaller font: Podcast

looking for something that pops with a medium to light blue background. text can be in white/red/orange colors. prefer solid colors for text, but background can vary.
I'm really open to other ideas too, sometimes you don't know what you want until you see it.

Target Market(s)

ecommerce business owners, managers

Industry/Entity Type

news, business, ecommerce

Font styles to use
Sans Serif

Colors
0054AA
0677BA
7BADD7
CADEEF
E8F1F8
0094D4
00A9DD
6FCCEA
C7EBF8
E9F6FB
F0912C
F2A743
F7CA91
FBE8D2
FDF5EE
EB3D1F
EC4F4E
F09395
F8D3D4
FCEDEE

Requirements
Must have
• text: BRISK LOOP
Should not have
• no microphones, headsets/headphones, speakers, or other props like that.

```html
<!DOCTYPE html>
<html lang="en">
<head>
<meta charset="utf-8">
<title>Brisk Loop Podcast — Cover Art</title>
<link rel="stylesheet" href="https://fonts.googleapis.com/css2?family=Anton&family=Archivo+Black&display=swap">
<style>
  :root {
    --stage: #d9d9d9;
    --cover: #ffffff;
    --brand-red: #eb3d1f;
    --ink: #2a2a2a;
  }
  * { margin: 0; padding: 0; box-sizing: border-box; }
  html, body {
    width: 1200px;
    height: 675px;
    overflow: hidden;
    background: var(--stage);
  }
  .canvas {
    position: relative;
    width: 1200px;
    height: 675px;
    display: flex;
    align-items: center;
    justify-content: center;
  }
  .cover {
    width: 610px;
    height: 610px;
    background: var(--cover);
    overflow: hidden;
  }
  .cover svg { display: block; width: 100%; height: 100%; }
  .cover__title {
    font-family: "Anton", "Oswald", sans-serif;
    fill: var(--brand-red);
  }
  .cover__label {
    font-family: "Archivo Black", "Arial Black", sans-serif;
    fill: var(--ink);
  }
  .cover__rule { fill: var(--ink); }
</style>
</head>
<body>
  <main class="canvas">
    <section class="cover" aria-label="Brisk Loop Podcast cover art">
      <svg viewBox="0 0 975 975" xmlns="http://www.w3.org/2000/svg">
        <text class="cover__title" x="56" y="449" font-size="448"
              textLength="854" lengthAdjust="spacingAndGlyphs">BRISK</text>
        <text class="cover__title" x="56" y="858" font-size="448"
              textLength="854" lengthAdjust="spacingAndGlyphs">LOOP</text>
        <text class="cover__label" x="56" y="926" font-size="34"
              textLength="220" lengthAdjust="spacingAndGlyphs">PODCAST</text>
        <rect class="cover__rule" x="308" y="902" width="602" height="23"/>
      </svg>
    </section>
  </main>
</body>
</html>
```